Brand new letterhead, business card, email signature etc.

We are a financial company in London, UK. Our website is www.marlowvane.com. We're wanting a complete remodel of the company colours, letter head, business cards, email signatures, etc. Looking to keep the same font for the company name. I have upload a colour palette that we want to work with. We're looking for company letterhead for outgoing letters/ correspondence, letterhead for internal documentation, email signatures, e-letters. etc. Ultimately we will redesign the entire website also. It is important that our clients get a strong, secure, warm, trustworthy, solid feeling and first impression.
Updates

Designs look the same

Target Market(s)

Institutional investors, (ultra) high net worth individuals

Industry/Entity Type

Finance, Invesments banking.

Font styles to use
Other font styles liked:
• Current font is "Champagne & Limousines"

Requirements
Must have
• Must use the colours provided on the PDF uploaded to the portal. The purple = main colour. The red = accent colour.
Nice to have
• Nice to use same font as now for the company name "Corvane". Font is "Champagne & Limousines". Nice to have some reference to the old logo flower, but only subtle.
Should not have
• Do not use the colour red from our website. Use the colours provided on the colour palette PDF that I uploaded in the portal.

```html
<!DOCTYPE html>
<html lang="en">
<head>
<meta charset="utf-8">
<title>Corvane — Stationery Suite</title>
<link href="https://fonts.googleapis.com/css2?family=Jost:wght@300;400&family=Open+Sans:wght@400&display=swap" rel="stylesheet">
<style>
  :root{
    --backdrop:#d4d5d8;
    --paper:#ffffff;
    --accent:#e03a25;
    --plum:#2e0e1c;
    --ink:#1f1f1f;
    --muted:#6e6e6e;
    --photo-a:#c9d3d6;
    --photo-b:#8f9ca3;
    --sign-tone:#eef0f2;
  }
  *{margin:0;padding:0;box-sizing:border-box}
  html,body{width:1200px;height:1200px;overflow:hidden;background:var(--backdrop)}
  body{position:relative;font-family:"Open Sans",sans-serif;color:var(--ink)}
  .abs{position:absolute}
  .bands{position:absolute;left:0;top:0;width:100%;height:100%}
  .icon{fill:none;stroke:currentColor;stroke-width:2;stroke-linecap:round;stroke-linejoin:round}

  /* wordmark */
  .wordmark{display:flex;align-items:center}
  .wordmark .mark-square{border:1.5px solid var(--ink);flex:none}
  .wordmark .brand-name{font-family:"Jost",sans-serif;font-weight:300;text-transform:uppercase;color:var(--ink);line-height:1;white-space:nowrap}

  .hero-mark{left:334px;top:62px}
  .hero-mark .mark-square{width:121px;height:121px;margin-right:31px}
  .hero-mark .brand-name{font-size:72px;letter-spacing:.27em}

  .doc{position:absolute;background:var(--paper);box-shadow:0 10px 9px -6px rgba(0,0,0,.35)}
  .section-label{position:absolute;font-family:"Jost",sans-serif;font-weight:400;font-size:10.5px;color:var(--ink);letter-spacing:.02em}

  /* letterhead */
  .letterhead{left:69px;top:267px;width:565px;height:765px}
  .lh-web{left:64px;top:32px;display:flex;align-items:center;gap:5px;font-family:"Jost",sans-serif;font-weight:300;font-size:8.5px;color:var(--ink)}
  .lh-web svg{width:10px;height:10px;color:var(--ink)}
  .lh-mark{left:316px;top:45px}
  .lh-mark .mark-square{width:50px;height:50px;margin-right:12px;border-width:1px}
  .lh-mark .brand-name{font-size:31px;letter-spacing:.2em}
  .recipient{left:64px;top:200px;width:421px}
  .recipient-name{font-family:"Jost",sans-serif;font-weight:300;font-size:12.5px;color:var(--ink);margin-bottom:6px}
  .recipient-info{font-size:8.5px;line-height:11.9px;color:var(--muted)}
  .letter-date{position:absolute;right:0;bottom:0;font-size:8.5px;color:var(--muted)}
  .letter-body{left:64px;top:292px;width:421px;font-size:8.4px;line-height:11.9px;color:var(--muted);text-align:justify}
  .letter-body p{margin-bottom:11.9px}
  .signature-area{left:387px;top:589px;width:99px;height:30px;background:var(--sign-tone);border-radius:3px}
  .signer{right:80px;top:620px;text-align:right}
  .signer-name{font-family:"Jost",sans-serif;font-weight:400;font-size:10px;color:var(--ink);letter-spacing:.03em}
  .signer-role{font-family:"Jost",sans-serif;font-weight:300;font-size:9px;color:var(--muted);margin-top:2px;letter-spacing:.04em}
  .lh-footer-item{display:flex;align-items:center;gap:6px;color:#fff;font-family:"Jost",sans-serif;font-weight:300;font-size:9.6px;line-height:13px}
  .lh-footer-item svg{width:12px;height:12px;color:#fff}

  /* email signature */
  .email-sig{left:681px;top:509px;width:406px;height:128px}
  .es-mark{left:26px;top:31px}
  .es-mark .mark-square{width:26px;height:26px;margin-right:6px;border-width:1px}
  .es-mark .brand-name{font-size:16px;letter-spacing:.18em}
  .es-contacts{left:29px;top:78px;font-family:"Jost",sans-serif;font-weight:400;font-size:5.4px;line-height:7.2px;color:var(--ink)}
  .es-row{display:flex;align-items:flex-start;gap:4px;margin-bottom:1px}
  .es-row svg{width:6px;height:6px;color:var(--accent);margin-top:1px;flex:none}
  .es-photo{left:247px;top:20px;width:76px;height:76px;border-radius:50%;background:radial-gradient(circle at 50% 40%,var(--photo-a),var(--photo-b))}
  .es-person{left:237px;top:99px;width:100px;text-align:center}
  .person-name{font-family:"Jost",sans-serif;font-weight:300;color:var(--accent);line-height:1;text-transform:uppercase}
  .person-role{font-family:"Jost",sans-serif;font-weight:300;color:var(--ink);line-height:1.1}
  .es-person .person-name{font-size:11px}
  .es-person .person-role{font-size:8px}

  /* business cards */
  .card-back{left:682px;top:699px;width:243px;height:139px}
  .cb-mark{left:52px;top:52px}
  .cb-mark .mark-square{width:35px;height:35px;margin-right:8px;border-width:1px}
  .cb-mark .brand-name{font-size:22px;letter-spacing:.18em}
  .cb-web{left:39px;top:128px;display:flex;align-items:center;gap:2px;color:#fff;font-family:"Jost",sans-serif;font-weight:400;font-size:5.6px}
  .cb-web svg{width:5px;height:5px;color:#fff}

  .card-front{left:682px;top:892px;width:243px;height:140px}
  .cf-mark{left:19px;top:56px}
  .cf-mark .mark-square{width:28px;height:28px;margin-right:6px;border-width:1px}
  .cf-mark .brand-name{font-size:17.5px;letter-spacing:.18em}
  .cf-person{right:24px;top:28px;text-align:right}
  .cf-person .person-name{font-size:11px}
  .cf-person .person-role{font-size:8px;margin-top:1px}
  .cf-contacts{right:7px;top:64px;font-family:"Jost",sans-serif;font-weight:300;font-size:6px;line-height:7.6px;color:var(--ink);text-align:right}
  .cf-row{display:flex;justify-content:flex-end;align-items:flex-start;gap:9px;margin-bottom:7px}
  .cf-row:last-child{margin-bottom:0}
  .cf-row svg{width:7px;height:7px;color:var(--accent);flex:none;margin-top:1px}
</style>
</head>
<body>

<svg width="0" height="0" style="position:absolute" aria-hidden="true">
  <symbol id="ico-phone" viewBox="0 0 24 24"><path d="M5 3h3.5l2 5-2.5 1.5a11 11 0 0 0 6.5 6.5L16 13.5l5 2V19a2 2 0 0 1-2 2A16 16 0 0 1 3 5a2 2 0 0 1 2-2z" fill="currentColor" stroke="none"/></symbol>
  <symbol id="ico-mail" viewBox="0 0 24 24"><rect x="2.5" y="5" width="19" height="14" rx="1.5" class="icon"/><path d="M3 6l9 7 9-7" class="icon"/></symbol>
  <symbol id="ico-mail-solid" viewBox="0 0 24 24"><rect x="2" y="5" width="20" height="14" rx="1.5" fill="currentColor"/><path d="M3 6.5l9 6.5 9-6.5" fill="none" stroke="#fff" stroke-width="1.8"/></symbol>
  <symbol id="ico-pin" viewBox="0 0 24 24"><path d="M12 22s7-7.2 7-12.5A7 7 0 0 0 5 9.5C5 14.8 12 22 12 22z" class="icon"/><circle cx="12" cy="9.5" r="2.6" class="icon"/></symbol>
  <symbol id="ico-globe" viewBox="0 0 24 24"><circle cx="12" cy="12" r="9.5" class="icon"/><path d="M2.5 12h19M12 2.5c3 3 3 16 0 19M12 2.5c-3 3-3 16 0 19M4.5 7h15M4.5 17h15" class="icon" stroke-width="1.5"/></symbol>
</svg>

<!-- brand lockup -->
<div class="wordmark hero-mark abs">
  <span class="mark-square"></span>
  <span class="brand-name">Corvane</span>
</div>

<!-- letterhead -->
<section class="doc letterhead" aria-label="Letterhead">
  <svg class="bands" viewBox="0 0 941 1275" preserveAspectRatio="none" aria-hidden="true">
    <polygon points="0,87 392,87 475,0 548,0 413,142 0,142" fill="var(--accent)"/>
    <polygon points="575,0 941,0 941,29 590,29 572,47 530,47" fill="var(--plum)"/>
    <polygon points="0,1213 467,1213 502,1177 593,1177 495,1275 0,1275" fill="var(--accent)"/>
    <polygon points="518,1275 578,1213 941,1213 941,1275" fill="var(--plum)"/>
    <polygon points="616,1177 705,1177 688,1195 597,1195" fill="var(--accent)"/>
  </svg>

  <div class="lh-web abs"><svg><use href="#ico-globe"/></svg>urwebsitename.com</div>

  <div class="wordmark lh-mark abs">
    <span class="mark-square"></span>
    <span class="brand-name">Corvane</span>
  </div>

  <div class="recipient abs">
    <div class="recipient-name">Name Surname</div>
    <div class="recipient-info">
      Senior Executive<br>
      Address goes here. Street, City, Country<br>
      contact@yourmail.com<br>
      000-987-654-321
    </div>
    <div class="letter-date">Date, 21 September, 2030</div>
  </div>

  <div class="letter-body abs">
    <p>Lorem ipsum dolor sit amet, consectetur adipisicing elit, sed do eiusmod tempor incididunt ut labore et dolore magna aliqua. Ut enim ad minim veniam, quis nostrud exercitation ullamco laboris nisi ut aliquip ex ea commodo consequat. Duis aute irure dolor in reprehenderit in voluptate velit esse cillum dolore eu fugiat nulla pariatur. Excepteur sint occaecat cupidatat non proident, sunt in culpa qui officia deserunt mollit anim id est laborum. Sed ut perspiciatis unde omnis iste natus error sit voluptatem accusantium doloremque laudantium, totam rem aperiam, eaque ipsa quae ab illo inventore veritatis et quasi architecto beatae vitae dicta sunt explicabo. Nemo enim ipsam voluptatem quia voluptas sit aspernatur aut odit aut fugit, sed quia consequuntur magni dolores eos qui ratione voluptatem sequi nesciunt. Neque porro voluptatem sequi nesciunt. Nemo enim ipsam voluptatem quia voluptas.</p>
    <p>Lorem ipsum dolor sit amet, consectetur adipisicing elit, sed do eiusmod tempor incididunt ut labore et dolore magna aliqua. Ut enim ad minim veniam, quis nostrud exercitation ullamco laboris nisi ut aliquip ex ea commodo consequat. Duis aute irure dolor in reprehenderit in voluptate velit esse cillum dolore eu fugiat nulla pariatur. Excepteur sint occaecat cupidatat non proident, sunt in culpa qui officia deserunt mollit anim id est laborum. Sed ut perspiciatis unde omnis iste natus error sit voluptatem accusantium doloremque laudantium, totam rem aperiam, eaque ipsa quae ab illo inventore veritatis et quasi architecto beatae vitae dicta sunt explicabo. Nemo enim ipsam voluptatem quia voluptas sit aspernatur aut odit aut.</p>
    <p>Lorem ipsum dolor sit amet, consectetur adipisicing elit, sed do eiusmod tempor incididunt ut labore et dolore magna aliqua. Ut enim ad minim veniam, quis nostrud exercitation ullamco laboris nisi ut aliquip ex ea commodo consequat. .</p>
  </div>

  <div class="signature-area abs" role="img" aria-label="Handwritten signature of Elliot Crane"></div>
  <div class="signer abs">
    <div class="signer-name">Elliot Crane</div>
    <div class="signer-role">Manager</div>
  </div>

  <div class="lh-footer-item abs" style="left:37px;top:731px">
    <svg><use href="#ico-phone"/></svg>
    <span>123. 456. 789078<br>555 452 211 23</span>
  </div>
  <div class="lh-footer-item abs" style="left:176px;top:738px">
    <svg><use href="#ico-mail"/></svg>
    <span>urname@email here</span>
  </div>
  <div class="lh-footer-item abs" style="left:361px;top:731px">
    <svg><use href="#ico-pin"/></svg>
    <span>Head Office:<br>Address Here, suite</span>
  </div>
</section>

<!-- email signature -->
<div class="section-label" style="left:681px;top:489px">Email Signature</div>
<section class="doc email-sig" aria-label="Email signature">
  <svg class="bands" viewBox="0 0 676 214" preserveAspectRatio="none" aria-hidden="true">
    <polygon points="0,0 272,0 245,27 0,27" fill="var(--accent)"/>
    <polygon points="285,0 676,0 676,13 296,13 277,24 263,24" fill="var(--plum)"/>
  </svg>
  <div class="wordmark es-mark abs">
    <span class="mark-square"></span>
    <span class="brand-name">Corvane</span>
  </div>
  <div class="es-contacts abs">
    <div class="es-row"><svg><use href="#ico-phone"/></svg><span>123. 456. 789078<br>+555 452 211 23</span></div>
    <div class="es-row"><svg><use href="#ico-mail-solid"/></svg><span>urname@email.com</span></div>
    <div class="es-row"><svg><use href="#ico-pin"/></svg><span>Head Office:<br>Address Here, suite</span></div>
  </div>
  <div class="es-photo abs" role="img" aria-label="Portrait photo of the director"></div>
  <div class="es-person abs">
    <div class="person-name">Elliot Crane</div>
    <div class="person-role">Director</div>
  </div>
</section>

<!-- business card back -->
<div class="section-label" style="left:683px;top:675px">Business Card back</div>
<section class="doc card-back" aria-label="Business card back">
  <svg class="bands" viewBox="0 0 406 232" preserveAspectRatio="none" aria-hidden="true">
    <polygon points="0,18 246,18 264,0 279,0 232,48 0,48" fill="var(--accent)"/>
    <polygon points="264,25 286,3 406,3 406,15 296,15 286,25" fill="var(--plum)"/>
    <polygon points="0,205 204,205 222,190 254,190 216,232 0,232" fill="var(--accent)"/>
    <polygon points="226,232 251,205 406,205 406,232" fill="var(--plum)"/>
    <polygon points="266,190 304,190 297,197 259,197" fill="var(--accent)"/>
  </svg>
  <div class="wordmark cb-mark abs">
    <span class="mark-square"></span>
    <span class="brand-name">Corvane</span>
  </div>
  <div class="cb-web abs"><svg><use href="#ico-globe"/></svg>urwebsitename.com</div>
</section>

<!-- business card front -->
<div class="section-label" style="left:683px;top:875px">Business Card front</div>
<section class="doc card-front" aria-label="Business card front">
  <svg class="bands" viewBox="0 0 406 233" preserveAspectRatio="none" aria-hidden="true">
    <polygon points="0,18 244,18 262,0 279,0 219,48 0,48" fill="var(--accent)"/>
    <polygon points="0,206 204,206 222,191 254,191 216,233 0,233" fill="var(--accent)"/>
    <polygon points="226,233 251,206 406,206 406,233" fill="var(--plum)"/>
    <polygon points="266,191 304,191 297,198 259,198" fill="var(--accent)"/>
  </svg>
  <div class="cf-person abs">
    <div class="person-name">Elliot Crane</div>
    <div class="person-role">Director</div>
  </div>
  <div class="wordmark cf-mark abs">
    <span class="mark-square"></span>
    <span class="brand-name">Corvane</span>
  </div>
  <div class="cf-contacts abs">
    <div class="cf-row"><span>123. 456. 789078</span><svg><use href="#ico-phone"/></svg></div>
    <div class="cf-row"><span>urname@email here</span><svg><use href="#ico-mail-solid"/></svg></div>
    <div class="cf-row"><span>Head Office:<br>Address Here, suite</span><svg><use href="#ico-pin"/></svg></div>
  </div>
</section>

</body>
</html>
```